UI/ UX Design for ERP Software

We need a new UX/UI interface for a ERP software for property managers. Our CMMS / ERP solution is made based on responsive design technologies and is coded in PHP.
The overall UX to be similar to Tev Ulna - easy navigation, intuitive menus.

Industry/Entity Type

Property Management

Number of Pages Required

5+ page

Requirements
Must have
• Round dock buttons
Consistent icons across the application
Enough Spacing between buttons/icons/ menu
Consistent Font
Nice to have
• We would like the UX to allow the users to use the application without /minimum training.
Should not have
• we don't want anything that is classic with respect to UX

```html
<!DOCTYPE html>
<html lang="en">
<head>
<meta charset="utf-8">
<title>Keystay Dashboard</title>
<link href="https://fonts.googleapis.com/css2?family=Open+Sans:wght@400;600;700&display=swap" rel="stylesheet">
<style>
:root{
  --sidebar:#0a7bff;
  --header-bg:#ebedf0;
  --accent:#0aa0f0;
  --tab-bg:#5eaee2;
  --tab-active:#0a7bff;
  --slate:#506177;
  --text:#4a5568;
  --muted:#6b7280;
  --grid:#e3e6ea;
  --card:#ffffff;
  --page:#f7f7f7;
  --bar:#5eaee2;
}
*{margin:0;padding:0;box-sizing:border-box}
html,body{width:1200px;height:625px;overflow:hidden}
body{font-family:"Open Sans",sans-serif;background:var(--page);position:relative;color:var(--text)}
.sidebar{position:absolute;left:0;top:0;width:140px;height:625px;background:var(--sidebar)}
.menu-toggle{position:absolute;left:50px;top:29px;width:35px}
.menu-toggle span{display:block;height:4px;border-radius:2px;background:#fff;margin-bottom:7px}
.topbar{position:absolute;left:140px;top:0;width:1060px;height:73px;background:var(--header-bg)}
.brand{position:absolute;left:172px;top:26px;display:flex;align-items:center;gap:7px;font-size:22px;font-weight:700;color:var(--sidebar)}
.brand-mark{width:16px;height:16px;background:var(--sidebar);border-radius:3px}
.search{position:absolute;left:313px;top:27px;width:182px;height:24px;border:1px solid #cfe0f5;background:#fff;display:flex}
.search input{flex:1;border:0;font:400 9px "Open Sans",sans-serif;padding-left:9px;color:var(--muted);outline:none;background:transparent}
.search button{width:27px;border:0;background:var(--tab-active);display:flex;align-items:center;justify-content:center}
.stat{position:absolute;top:17px}
.stat-label{font-size:9.5px;color:var(--text);letter-spacing:.2px}
.stat-value{margin-top:11px;display:flex;align-items:center;gap:6px;font-size:15px;font-weight:600;color:var(--accent);white-space:nowrap}
.divider{position:absolute;top:18px;width:1px;height:45px;background:#d6d9de}
.tabs{position:absolute;left:167px;top:73px;width:999px;height:34px;display:flex;background:var(--tab-bg)}
.tabs .spacer{width:225px;background:var(--slate)}
.tab{display:flex;align-items:center;justify-content:center;gap:4px;color:#fff;font-size:11.5px;padding:0 22px}
.tab.active{background:var(--tab-active);width:114px;padding:0}
.card{position:absolute;left:167px;top:107px;width:999px;height:463px;background:var(--card);border:1px solid #e6e8eb;border-top:0}
.footer{position:absolute;left:140px;top:589px;width:1060px;height:36px;background:var(--slate);color:#fff;font-size:7.5px;display:flex;align-items:center;justify-content:center}
.footer .code{position:absolute;right:10px}
</style>
</head>
<body>
<aside class="sidebar">
  <div class="menu-toggle"><span></span><span></span><span></span></div>
</aside>

<header class="topbar"></header>
<div class="brand"><span class="brand-mark"></span>Keystay</div>
<form class="search">
  <input type="text" placeholder="Search user" value="Search user">
  <button type="button" aria-label="Search">
    <svg width="8" height="8" viewBox="0 0 10 10"><circle cx="4" cy="4" r="3" fill="none" stroke="#fff" stroke-width="1.6"/><line x1="6.3" y1="6.3" x2="9" y2="9" stroke="#fff" stroke-width="1.8"/></svg>
  </button>
</form>

<div class="stat" style="left:523px">
  <div class="stat-label">PROPERTIES</div>
  <div class="stat-value"><svg width="13" height="11" viewBox="0 0 13 11"><path d="M6.5 0 13 5.5h-2V11H8V7.5H5V11H2V5.5H0z" fill="var(--accent)"/></svg>3</div>
</div>
<div class="divider" style="left:599px"></div>
<div class="stat" style="left:606px">
  <div class="stat-label">TENANTS</div>
  <div class="stat-value"><svg width="16" height="12" viewBox="0 0 16 12"><circle cx="8" cy="3" r="2.6" fill="var(--accent)"/><circle cx="3" cy="4" r="2" fill="var(--accent)"/><circle cx="13" cy="4" r="2" fill="var(--accent)"/><path d="M3.5 12c0-4 2-6 4.5-6s4.5 2 4.5 6z" fill="var(--accent)"/><path d="M0 10c0-3 1.3-4 3-4s2 .5 2.5 1L3 10z M16 10c0-3-1.3-4-3-4s-2 .5-2.5 1L13 10z" fill="var(--accent)"/></svg>8</div>
</div>
<div class="divider" style="left:676px"></div>
<div class="stat" style="left:683px">
  <div class="stat-label">TOTAL PROPERTIES AREA</div>
  <div class="stat-value"><svg width="14" height="14" viewBox="0 0 14 14"><path d="M7 0 9.5 3H8v3h3V4.5L14 7l-3 2.5V8H8v3h1.5L7 14l-2.5-3H6V8H3v1.5L0 7l3-2.5V6h3V3H4.5z" fill="var(--accent)"/></svg>422,000.00 SQ.FT.</div>
</div>
<div class="divider" style="left:850px"></div>
<div class="stat" style="left:857px">
  <div class="stat-label">RENTED AREA</div>
  <div class="stat-value"><svg width="14" height="14" viewBox="0 0 14 14"><path d="M7 0 9.5 3H8v3h3V4.5L14 7l-3 2.5V8H8v3h1.5L7 14l-2.5-3H6V8H3v1.5L0 7l3-2.5V6h3V3H4.5z" fill="var(--accent)"/></svg>233,500.00 SQ.FT.</div>
</div>
<div class="divider" style="left:1018px"></div>
<div class="stat" style="left:1025px">
  <div class="stat-label">VACANCIES AREA</div>
  <div class="stat-value"><svg width="14" height="14" viewBox="0 0 14 14"><path d="M7 0 9.5 3H8v3h3V4.5L14 7l-3 2.5V8H8v3h1.5L7 14l-2.5-3H6V8H3v1.5L0 7l3-2.5V6h3V3H4.5z" fill="var(--accent)"/></svg>188,500.00 SQ.FT.</div>
</div>

<nav class="tabs">
  <div class="spacer"></div>
  <div class="tab active"><svg width="10" height="10" viewBox="0 0 10 10"><circle cx="5" cy="5" r="4" fill="none" stroke="#fff" stroke-width="1.5"/><path d="M5 2.5V5h2" fill="none" stroke="#fff" stroke-width="1.2"/></svg>Last 7 days</div>
  <div class="tab"><svg width="10" height="10" viewBox="0 0 10 10"><circle cx="5" cy="5" r="4" fill="none" stroke="#fff" stroke-width="1.5"/><path d="M5 2.5V5h2" fill="none" stroke="#fff" stroke-width="1.2"/></svg>Last months</div>
  <div class="tab"><svg width="10" height="10" viewBox="0 0 10 10"><circle cx="5" cy="5" r="4" fill="none" stroke="#fff" stroke-width="1.5"/><path d="M5 2.5V5h2" fill="none" stroke="#fff" stroke-width="1.2"/></svg>Last 3 months</div>
  <div class="tab"><svg width="10" height="10" viewBox="0 0 10 10"><circle cx="5" cy="5" r="4" fill="none" stroke="#fff" stroke-width="1.5"/><path d="M5 2.5V5h2" fill="none" stroke="#fff" stroke-width="1.2"/></svg>Next 7 days</div>
  <div class="tab"><svg width="10" height="10" viewBox="0 0 10 10"><circle cx="5" cy="5" r="4" fill="none" stroke="#fff" stroke-width="1.5"/><path d="M5 2.5V5h2" fill="none" stroke="#fff" stroke-width="1.2"/></svg>Next months</div>
  <div class="tab"><svg width="10" height="10" viewBox="0 0 10 10"><circle cx="5" cy="5" r="4" fill="none" stroke="#fff" stroke-width="1.5"/><path d="M5 2.5V5h2" fill="none" stroke="#fff" stroke-width="1.2"/></svg>Next 3 months</div>
</nav>

<section class="card"></section>
<svg class="chart" style="position:absolute;left:0;top:0" width="1200" height="589" font-family="Open Sans, sans-serif">
  <g fill="var(--slate)">
    <rect x="204" y="136" width="2" height="13"/><rect x="208" y="141" width="2" height="8"/><rect x="212" y="138" width="2" height="11"/><rect x="216" y="143" width="2" height="6"/><rect x="204" y="148" width="18" height="1.5"/>
  </g>
  <text x="230" y="148" font-size="16.5" fill="var(--slate)">12/27/2020 - 01/03/2021</text>

  <g stroke="var(--grid)" stroke-width="0.8">
    <line x1="269" y1="188" x2="1166" y2="188"/>
    <line x1="269" y1="241" x2="1166" y2="241"/>
    <line x1="269" y1="295" x2="1166" y2="295"/>
    <line x1="269" y1="349" x2="1166" y2="349"/>
    <line x1="269" y1="403" x2="1166" y2="403"/>
  </g>
  <line x1="269" y1="456.5" x2="1166" y2="456.5" stroke="#cfd4da" stroke-width="1"/>
  <g stroke="#cfd4da" stroke-width="1">
    <line x1="269" y1="456" x2="269" y2="466"/><line x1="387" y1="456" x2="387" y2="466"/><line x1="489" y1="456" x2="489" y2="466"/><line x1="602" y1="456" x2="602" y2="466"/><line x1="715" y1="456" x2="715" y2="466"/><line x1="817" y1="456" x2="817" y2="466"/><line x1="935" y1="456" x2="935" y2="466"/><line x1="1048" y1="456" x2="1048" y2="466"/><line x1="1166" y1="456" x2="1166" y2="466"/>
  </g>
  <g fill="var(--slate)"><rect x="230" y="185" width="10" height="1.3"/><rect x="230" y="187.5" width="10" height="1.3"/><rect x="230" y="190" width="10" height="1.3"/></g>
  <g font-size="9.5" fill="var(--muted)">
    <text x="243" y="191">1.25</text>
    <text x="243" y="245">1</text>
    <text x="243" y="298">0.75</text>
    <text x="243" y="352">0.5</text>
    <text x="243" y="406">0.25</text>
    <text x="243" y="460">0</text>
  </g>
  <text transform="translate(216 354) rotate(-90)" font-size="12" fill="var(--muted)">Number</text>
  <rect x="620" y="241" width="12" height="215" fill="var(--bar)"/>
  <g font-size="8.5" fill="var(--muted)" text-anchor="middle">
    <text x="325" y="477">12/27/2020</text><text x="435" y="477">12/28/2020</text><text x="546" y="477">12/29/2020</text><text x="656" y="477">12/30/2020</text><text x="767" y="477">12/31/2020</text><text x="877" y="477">01/01/2021</text><text x="988" y="477">01/02/2021</text><text x="1098" y="477">01/03/2021</text>
  </g>
  <g font-size="7.5" font-weight="700" fill="#3b4250">
    <rect x="267" y="503" width="9" height="8" fill="#7cb5ec"/><text x="279" y="510">Scheduled Maintenance</text>
    <rect x="376" y="503" width="9" height="8" fill="#90ed7d"/><text x="388" y="510">Completed Scheduled Maintenance</text>
    <rect x="529" y="503" width="9" height="8" fill="#f7a35c"/><text x="541" y="510">Future Scheduled Maintenance</text>
    <rect x="665" y="503" width="9" height="8" fill="#434348"/><text x="677" y="510">Scheduled Work Orders</text>
    <rect x="773" y="503" width="9" height="8" fill="#8085e9"/><text x="785" y="510">Completed Work Orders</text>
    <rect x="883" y="503" width="9" height="8" fill="#f15c80"/><text x="895" y="510">Property Inspections in Progress</text>
    <rect x="1025" y="503" width="9" height="8" fill="#e4d354"/><text x="1037" y="510">Completed Property Inspections</text>
  </g>
</svg>

<footer class="footer">© 2021 Keystay . All right reserved.&nbsp; Term of Use<span class="code">C16</span></footer>
</body>
</html>
```